Valdane Companies Business Card Design

We need a new business card for our Private Equity Real Estate Development firm, “Valdane” and our EB-5 regional center “Thornmere Regional Center” on one card. We prefer a design that is simple, elegant, and represents the luxury products we design and build as well as the financial security and stability our successful history has produced. We are an industry leader in our field and 3rd generation family business that has evolved into an institutional quality investment platform. Considered design size is standard business card dimensions (3.5 x 2 inches with an additional 1/8 inch space for design elements or backgrounds that extend beyond the finished size of your piece.

Target Market(s)

• High net worth individuals
• Highly skilled technical workers and physicians in the US seeking investment-based immigration opportunities
• Sophisticated private equity investors
• Intermediary partners include domestic attorneys and investment brokers, as well as international agent networks
• US real estate developers

Industry/Entity Type

Finance

Contact Information for Business Card

(Providing placeholder info for personal information, please design for longer character spaces, longer names and addresses etc..)
• Logo for Valdane
• Logo for Thornmere Regional Center
• Full name: Marcus Valdane
• Job title: CEO
• Email address: mvaldane@valdanecompanies.com
• Cell phone number: +1.555.314.2287
• Office number +1.555.628.4410
• Office address: Larkfield Court 5, 4817 Vista Orilla, Calder Springs, CA.
• Website: www.valdanecompanies.com

Font styles to use
Serif
Sans Serif

Colors
ec1f27
ffffff
000000

Requirements
Must have
• • Logo for Valdane
• • Logo for Thornmere Regional Center
• - Use rounded corners
• (See .ai file included for logos)
Nice to have
• • Simple, elegant design
• • Aesthetically compatible with our website design (www.valdanecompanies.com)
• • Color palette including but not limited to white, black, and red (as per logos)
Should not have
• - Not too much red color
• - Do not stack both logos on top of each other

```html
<!DOCTYPE html>
<html lang="en">
<head>
<meta charset="utf-8">
<title>Valdane Companies Business Cards</title>
<link rel="stylesheet" href="https://fonts.googleapis.com/css2?family=Crimson+Text:wght@400;600&family=Montserrat:wght@400;500&display=swap">
<style>
  :root {
    --bg: #e6e1d9;
    --divider: #ffffff;
    --card-white: #ffffff;
    --charcoal: #3a3a3b;
    --charcoal-light: #4a4a4b;
    --maroon: #a31b2e;
    --maroon-light: #b3283b;
    --ink: #2b2b2b;
    --ink-soft: #555555;
    --silver: #e4e4e4;
    --silver-dark: #c9c9c9;
    --serif: "Crimson Text", Georgia, serif;
    --sans: "Montserrat", Arial, sans-serif;
  }
  * { box-sizing: border-box; margin: 0; padding: 0; }
  html, body { width: 800px; height: 1200px; overflow: hidden; }
  body { background: var(--divider); font-family: var(--serif); }

  .sheet { position: relative; width: 800px; height: 596px; background: var(--bg); }
  .sheet + .sheet { margin-top: 8px; }

  .card {
    position: absolute;
    width: 440px;
    height: 252px;
    border-radius: 12px;
    overflow: hidden;
    box-shadow: 0 6px 18px rgba(0,0,0,0.18);
  }
  .card-front { left: 60px; top: 50px; color: var(--card-white); }
  .card-back  { left: 300px; top: 300px; background: var(--card-white); color: var(--ink); }

  .theme-capital .card-front { background: linear-gradient(135deg, var(--charcoal-light), var(--charcoal)); }
  .theme-center  .card-front { background: linear-gradient(135deg, var(--maroon-light), var(--maroon)); }
  .theme-capital { --accent: var(--charcoal); }
  .theme-center  { --accent: var(--maroon); }

  /* front */
  .front-brand {
    position: absolute; inset: 0;
    display: flex; flex-direction: column; align-items: center; justify-content: center;
    gap: 14px;
  }
  .front-mark { width: 40px; height: 40px; background: var(--card-white); opacity: .9; border-radius: 3px; }
  .front-name { font-family: var(--serif); font-weight: 600; font-size: 44px; letter-spacing: 2px; text-transform: uppercase; line-height: 1; text-align: center; }
  .front-name small { display: block; font-size: 12px; letter-spacing: 7px; margin-top: 6px; font-weight: 600; }

  /* back */
  .accent-strip-left { position: absolute; left: 0; bottom: 0; width: 9px; height: 42%; background: var(--accent); }
  .accent-strip-right { position: absolute; right: 0; top: 0; width: 9px; height: 30%; background: var(--accent); }

  .back-brand { position: absolute; left: 26px; top: 66px; display: flex; align-items: center; gap: 10px; }
  .back-mark { width: 22px; height: 22px; background: var(--accent); border-radius: 2px; }
  .back-rule { width: 1px; height: 32px; background: var(--accent); }
  .back-name { font-family: var(--serif); font-weight: 600; font-size: 22px; letter-spacing: 1px; text-transform: uppercase; line-height: 1; color: var(--accent); }
  .back-name small { display: block; font-size: 7px; letter-spacing: 4px; margin-top: 3px; font-weight: 600; }

  .person { position: absolute; right: 28px; top: 20px; text-align: right; }
  .person-name { font-family: var(--serif); font-weight: 600; font-size: 19px; color: var(--ink); }
  .person-title { font-family: var(--sans); font-size: 9px; letter-spacing: 2px; color: var(--accent); margin-top: -2px; }

  .decor-block {
    position: absolute; right: 40px; top: 70px; width: 120px; height: 110px;
    border-radius: 6px;
    background: linear-gradient(135deg, var(--silver), var(--silver-dark));
    opacity: .7;
  }

  .contact-list { position: absolute; left: 26px; bottom: 22px; list-style: none; font-size: 12px; line-height: 16px; color: var(--ink-soft); }
  .contact-list li { display: flex; align-items: center; gap: 8px; }
  .contact-list svg { width: 11px; height: 11px; flex: none; }
  .contact-list .address { padding-left: 19px; }
</style>
</head>
<body>

<section class="sheet theme-capital">
  <div class="card card-front">
    <div class="front-brand">
      <div class="front-mark"></div>
      <div class="front-name">Valdane<small>Capital</small></div>
    </div>
  </div>
  <div class="card card-back">
    <div class="accent-strip-left"></div>
    <div class="accent-strip-right"></div>
    <div class="person"><div class="person-name">Marcus Valdane</div><div class="person-title">CEO</div></div>
    <div class="decor-block" aria-hidden="true"></div>
    <div class="back-brand"><div class="back-mark"></div><div class="back-rule"></div><div class="back-name">Valdane<small>Capital</small></div></div>
    <ul class="contact-list">
      <li><svg viewBox="0 0 12 12"><rect x="3" y="0.5" width="6" height="11" rx="1" fill="none" stroke="currentColor"/><rect x="5" y="9" width="2" height="1" fill="currentColor"/></svg>+1.555.314.2287</li>
      <li><svg viewBox="0 0 12 12"><path d="M1 4 Q6 0 11 4 L9 5 L8 3.5 L4 3.5 L3 5 Z" fill="currentColor"/><rect x="2" y="6" width="8" height="5" rx="1" fill="currentColor"/></svg>+1.555.628.4410</li>
      <li><svg viewBox="0 0 12 12"><rect x="0.5" y="2" width="11" height="8" fill="none" stroke="currentColor"/><path d="M0.5 2 L6 7 L11.5 2" fill="none" stroke="currentColor"/></svg>mvaldane@valdanecompanies.com</li>
      <li><svg viewBox="0 0 12 12"><circle cx="6" cy="6" r="5.5" fill="none" stroke="currentColor"/><path d="M0.5 6 H11.5 M6 0.5 Q2.5 6 6 11.5 M6 0.5 Q9.5 6 6 11.5" fill="none" stroke="currentColor"/></svg>www.valdanecompanies.com</li>
      <li class="address">Larkfield Court 5, 4817 Vista Orilla</li>
      <li class="address">Calder Springs, CA</li>
    </ul>
  </div>
</section>

<section class="sheet theme-center">
  <div class="card card-front">
    <div class="front-brand">
      <div class="front-mark"></div>
      <div class="front-name">Thornmere<small>Regional Center</small></div>
    </div>
  </div>
  <div class="card card-back">
    <div class="accent-strip-left"></div>
    <div class="accent-strip-right"></div>
    <div class="person"><div class="person-name">Marcus Valdane</div><div class="person-title">CEO</div></div>
    <div class="decor-block" aria-hidden="true"></div>
    <div class="back-brand"><div class="back-mark"></div><div class="back-rule"></div><div class="back-name">Thornmere<small>Regional Center</small></div></div>
    <ul class="contact-list">
      <li><svg viewBox="0 0 12 12"><rect x="3" y="0.5" width="6" height="11" rx="1" fill="none" stroke="currentColor"/><rect x="5" y="9" width="2" height="1" fill="currentColor"/></svg>+1.555.314.2287</li>
      <li><svg viewBox="0 0 12 12"><path d="M1 4 Q6 0 11 4 L9 5 L8 3.5 L4 3.5 L3 5 Z" fill="currentColor"/><rect x="2" y="6" width="8" height="5" rx="1" fill="currentColor"/></svg>+1.555.628.4410</li>
      <li><svg viewBox="0 0 12 12"><rect x="0.5" y="2" width="11" height="8" fill="none" stroke="currentColor"/><path d="M0.5 2 L6 7 L11.5 2" fill="none" stroke="currentColor"/></svg>mvaldane@valdanecompanies.com</li>
      <li><svg viewBox="0 0 12 12"><circle cx="6" cy="6" r="5.5" fill="none" stroke="currentColor"/><path d="M0.5 6 H11.5 M6 0.5 Q2.5 6 6 11.5 M6 0.5 Q9.5 6 6 11.5" fill="none" stroke="currentColor"/></svg>www.valdanecompanies.com</li>
      <li class="address">Larkfield Court 5, 4817 Vista Orilla</li>
      <li class="address">Calder Springs, CA</li>
    </ul>
  </div>
</section>

</body>
</html>
```